Accounting business needs business card

I have a business card but need something better. I want the colour changed and the design to be better. I have uploaded a picture of my new sign that is grey in colour, i would like to incorporate these colours.

```html
<!DOCTYPE html>
<html lang="en">
<head>
<meta charset="utf-8">
<title>Clearline Tax – Business Cards</title>
<link href="https://fonts.googleapis.com/css2?family=Montserrat:wght@500;700&family=Questrial&display=swap" rel="stylesheet">
<style>
  :root {
    --page: #e9eaec;
    --brand-blue: #4a72b8;
    --charcoal: #2a2d32;
    --ink: #1f2125;
    --white: #ffffff;
    --badge-blue: #1f5aa6;
    --badge-gold: #f3c623;
    --badge-cyan: #1fb6e8;
  }
  * { box-sizing: border-box; margin: 0; padding: 0; }
  html, body { width: 1200px; height: 965px; overflow: hidden; }
  body {
    background: var(--page);
    font-family: "Questrial", sans-serif;
    position: relative;
  }
  .card {
    position: absolute;
    left: 250px;
    width: 700px;
    height: 400px;
    overflow: hidden;
    box-shadow: 0 10px 30px rgba(0,0,0,.18);
  }
  .card-front { top: 60px; background: var(--brand-blue); }
  .card-back { top: 505px; background: var(--white); }

  .brand-mark {
    display: flex;
    flex-direction: column;
    align-items: center;
    position: absolute;
  }
  .brand-dot {
    border-radius: 50%;
    border: 3px solid currentColor;
  }
  .brand-name {
    font-family: "Montserrat", sans-serif;
    font-weight: 500;
    white-space: nowrap;
  }
  .card-front .brand-mark { color: var(--white); left: 0; right: 0; top: 95px; }
  .card-front .brand-dot { width: 110px; height: 110px; margin-bottom: 30px; }
  .card-front .brand-name { font-size: 40px; letter-spacing: .42em; margin-right: -.42em; }

  .card-back .brand-mark { color: var(--ink); right: 40px; top: 24px; }
  .card-back .brand-dot { width: 76px; height: 76px; margin-bottom: 14px; }
  .card-back .brand-name { font-size: 24px; letter-spacing: .3em; margin-right: -.3em; }

  .back-shapes { position: absolute; inset: 0; }

  .person { position: absolute; left: 40px; top: 150px; color: var(--ink); }
  .person-name {
    font-family: "Montserrat", sans-serif;
    font-weight: 700;
    font-size: 30px;
    color: var(--brand-blue);
    line-height: 1.1;
  }
  .person-creds, .person-role { font-size: 17px; line-height: 1.35; }

  .contact {
    position: absolute;
    right: 34px;
    top: 258px;
    list-style: none;
    color: var(--white);
    font-size: 16px;
    text-align: right;
  }
  .contact li { display: flex; align-items: center; justify-content: flex-end; gap: 10px; line-height: 1.55; }
  .contact svg { width: 15px; height: 15px; }

  .accreditation {
    position: absolute;
    left: 40px;
    bottom: 22px;
    display: flex;
    align-items: center;
    gap: 14px;
    color: var(--white);
  }
  .badge-block { display: flex; width: 150px; height: 52px; }
  .badge-block span:first-child { flex: 3; background: var(--badge-blue); }
  .badge-block span:last-child { flex: 2; background: var(--badge-gold); }
  .accreditation-note { font-size: 15px; line-height: 1.2; }
  .partner-circle { width: 60px; height: 60px; border-radius: 50%; background: var(--badge-cyan); }
</style>
</head>
<body>

  <section class="card card-front" aria-label="Card front">
    <div class="brand-mark">
      <span class="brand-dot"></span>
      <span class="brand-name">CLEARLINE TAX</span>
    </div>
  </section>

  <section class="card card-back" aria-label="Card back">
    <svg class="back-shapes" viewBox="0 0 700 400" width="700" height="400" aria-hidden="true">
      <path d="M0,280 Q380,262 700,175 Q400,290 0,306 Z" fill="var(--brand-blue)"/>
      <path d="M0,318 Q400,300 700,192 L700,400 L0,400 Z" fill="var(--charcoal)"/>
    </svg>

    <div class="brand-mark">
      <span class="brand-dot"></span>
      <span class="brand-name">CLEARLINE TAX</span>
    </div>

    <div class="person">
      <p class="person-name">Dane Whitford</p>
      <p class="person-creds">CPA, MTAX, BCOM (Acc &amp; Fin)</p>
      <p class="person-role">Taxation and Business Accountant</p>
    </div>

    <ul class="contact">
      <li>0400 555 018
        <svg viewBox="0 0 24 24" fill="none" stroke="currentColor" stroke-width="2"><path d="M5 3h4l2 5-3 2a11 11 0 0 0 6 6l2-3 5 2v4a2 2 0 0 1-2 2A17 17 0 0 1 3 5a2 2 0 0 1 2-2z"/></svg>
      </li>
      <li>dane@clearlinetax.com.au
        <svg viewBox="0 0 24 24" fill="none" stroke="currentColor" stroke-width="2"><rect x="3" y="5" width="18" height="14"/><path d="M3 5l9 8 9-8"/></svg>
      </li>
      <li>www.clearlinetax.com.au
        <svg viewBox="0 0 24 24" fill="none" stroke="currentColor" stroke-width="2"><circle cx="12" cy="12" r="9"/><path d="M3 12h18M12 3c3 3 3 15 0 18M12 3c-3 3-3 15 0 18"/></svg>
      </li>
    </ul>

    <div class="accreditation">
      <div class="badge-block" role="img" aria-label="Professional body membership badge"><span></span><span></span></div>
      <p class="accreditation-note">Clearline Tax is an<br>Accredited Practice</p>
      <span class="partner-circle" role="img" aria-label="Software partner badge"></span>
    </div>
  </section>

</body>
</html>
```